FREE Network Assessment image for landing page

This graphic will be on a landing page and on the left will be Text and a download button that we change and control. The graphic for this project will be to the right.
I will add an example of the landing page area so that it makes more sense.

Please include the text from the sample - the font needs to be the same style as what we are using on the left side!

The graphic needs to be a .png file, roughly 713 x 527 white background. Use discretion on design layout.

Colors are black, Red = PMS 1795 and Gray = Cool Gray 10

Thanks,
Tom Garrick

Target Market(s)

small businesses

Industry/Entity Type

Information Technology

Font styles to use
Other font styles liked:
• See sample

Requirements
Must have
• see description
Nice to have
• Possibly small technology related image to help enhance the text but I don't want any image to compete with the text. Keep in mind the colors mentioned in the description - this is the web site colors.
Should not have
• Should not be hard to read

```html
<!DOCTYPE html>
<html lang="en">
<head>
<meta charset="utf-8">
<title>Free Network Health Assessment</title>
<link rel="stylesheet" href="https://fonts.googleapis.com/css2?family=Oswald:wght@300;400;500&family=Lato:wght@400&display=swap">
<style>
  :root {
    --brand-red: #e23536;
    --button-red: #ef4647;
    --text-red: #e8383d;
    --soft-red: #ea5455;
    --cool-gray: #454649;
    --nav-active: #6a6a6a;
    --ink: #111111;
    --page: #ffffff;
    --dot: #e4e4e6;
    --dot-ring: #c9cbe8;
  }
  * { margin: 0; padding: 0; box-sizing: border-box; }
  html, body { width: 1200px; height: 554px; overflow: hidden; background: var(--page); }
  .canvas { position: relative; width: 1200px; height: 554px; overflow: hidden; }

  .main-nav {
    position: absolute; left: 14px; top: 0; width: 1182px; height: 46px;
    background: var(--brand-red); border-radius: 0 0 6px 6px;
    box-shadow: 0 2px 4px rgba(0,0,0,.25);
  }
  .nav-item {
    position: absolute; top: 0; height: 46px; line-height: 34px;
    font-family: 'Oswald', sans-serif; font-weight: 500; font-size: 16px;
    color: #fff; letter-spacing: .2px; white-space: nowrap; transform: translateX(-50%);
  }
  .nav-item.is-active {
    background: var(--nav-active); width: 87px; text-align: center;
  }
  .nav-item .chevron { display: inline-block; margin-left: 6px; vertical-align: 2px; }
  .nav-search { position: absolute; left: 1094px; top: 9px; }

  .hero-title {
    position: absolute; left: 14px; top: 130px;
    font-family: 'Oswald', sans-serif; font-weight: 300; font-size: 64px;
    line-height: 70px; color: var(--cool-gray); letter-spacing: .5px;
  }
  .hero-lead {
    position: absolute; left: 14px; top: 312px; width: 640px;
    font-family: 'Lato', sans-serif; font-size: 20.5px; line-height: 28px;
    color: var(--soft-red);
  }
  .cta-button {
    position: absolute; left: 14px; top: 394px; width: 227px; height: 44px;
    border-radius: 22px; background: var(--button-red);
    font-family: 'Oswald', sans-serif; font-weight: 400; font-size: 17px;
    color: #fff; line-height: 44px; text-align: center;
  }
  .slider-dots { position: absolute; left: 0; top: 0; }
  .slider-dot {
    position: absolute; width: 12px; height: 12px; border-radius: 50%;
    background: var(--dot); top: 522px;
  }
  .slider-dot.is-current {
    background: var(--brand-red); box-shadow: 0 0 0 5px var(--dot-ring);
  }

  .service-card { position: absolute; left: 680px; top: 0; width: 480px; height: 554px; }
  .service-title {
    position: absolute; left: 0; top: 110px; width: 480px; text-align: center;
    font-family: 'Oswald', sans-serif; font-weight: 400; font-size: 37px;
    line-height: 42px; color: var(--cool-gray);
  }
  .service-icon {
    position: absolute; left: 192px; top: 208px; width: 126px; height: 64px;
    background: linear-gradient(90deg, #1a1a1a 0 62%, #e23536 62% 100%);
    opacity: .85; border-radius: 4px;
  }
  .service-list { position: absolute; left: 14px; top: 286px; list-style: none; }
  .service-list li {
    position: relative; padding-left: 17px; margin-bottom: 5px;
    font-family: 'Lato', sans-serif; font-size: 16.5px; line-height: 19.5px;
    color: var(--text-red); white-space: nowrap;
  }
  .service-list li svg { position: absolute; left: -1px; top: 3px; }
  .service-cta {
    position: absolute; left: 0; top: 482px; width: 480px; text-align: center;
    font-family: 'Oswald', sans-serif; font-weight: 400; font-size: 27px;
    line-height: 34px; color: var(--ink);
  }
</style>
</head>
<body>
<div class="canvas">
  <nav class="main-nav">
    <span class="nav-item is-active" style="left:116px">HOME</span>
    <span class="nav-item" style="left:207px">ABOUT</span>
    <span class="nav-item" style="left:296px">TEAM</span>
    <span class="nav-item" style="left:459px">WHAT MAKES US DIFFERENT<svg class="chevron" width="8" height="6" viewBox="0 0 8 6"><path d="M1 1l3 3 3-3" stroke="#fff" stroke-width="2" fill="none"/></svg></span>
    <span class="nav-item" style="left:642px">SERVICES</span>
    <span class="nav-item" style="left:771px">DEPARTMENTS</span>
    <span class="nav-item" style="left:894px">BLOG<svg class="chevron" width="8" height="6" viewBox="0 0 8 6"><path d="M1 1l3 3 3-3" stroke="#fff" stroke-width="2" fill="none"/></svg></span>
    <span class="nav-item" style="left:998px">CONTACTS</span>
    <svg class="nav-search" width="16" height="16" viewBox="0 0 16 16" aria-label="Search"><circle cx="6.5" cy="6.5" r="4.5" stroke="#fff" stroke-width="2.4" fill="none"/><path d="M10 10l4.5 4.5" stroke="#fff" stroke-width="2.8" stroke-linecap="round"/></svg>
  </nav>

  <h1 class="hero-title">FREE NETWORK HEALTH<br>ASSESSMENT TOOL</h1>
  <p class="hero-lead">Let us show you how to find and get rid of computer and network slowness, security vulnerabilities and potential disasters.</p>
  <div class="cta-button">MAKE AN APPOINTMENT</div>

  <div class="slider-dots">
    <span class="slider-dot" style="left:21px"></span>
    <span class="slider-dot" style="left:60px"></span>
    <span class="slider-dot is-current" style="left:98px"></span>
  </div>

  <section class="service-card">
    <h2 class="service-title">FREE NETWORK &amp; COMPUTER<br>HEALTH CHECK SERVICE</h2>
    <div class="service-icon" role="img" aria-label="Icon of a computer monitor showing a bar chart under a magnifying glass"></div>
    <ul class="service-list">
      <li><svg width="14" height="14" viewBox="0 0 14 14"><circle cx="7" cy="7" r="7" fill="#333"/><path d="M5.5 4l3 3-3 3" stroke="#fff" stroke-width="2" fill="none"/></svg>Check your network’s security against hacker attacks, theft,<br>&nbsp;ransomware, viruses, and more.</li>
      <li><svg width="14" height="14" viewBox="0 0 14 14"><circle cx="7" cy="7" r="7" fill="#333"/><path d="M5.5 4l3 3-3 3" stroke="#fff" stroke-width="2" fill="none"/></svg>See who and what has access to your network and data.</li>
      <li><svg width="14" height="14" viewBox="0 0 14 14"><circle cx="7" cy="7" r="7" fill="#333"/><path d="M5.5 4l3 3-3 3" stroke="#fff" stroke-width="2" fill="none"/></svg>Perform network and Internet speed test</li>
      <li><svg width="14" height="14" viewBox="0 0 14 14"><circle cx="7" cy="7" r="7" fill="#333"/><path d="M5.5 4l3 3-3 3" stroke="#fff" stroke-width="2" fill="none"/></svg>Resolve PC slowness issues, security vulnerabilities and<br>improper configurations</li>
      <li><svg width="14" height="14" viewBox="0 0 14 14"><circle cx="7" cy="7" r="7" fill="#333"/><path d="M5.5 4l3 3-3 3" stroke="#fff" stroke-width="2" fill="none"/></svg>Validate your backups are working and recoverable in a<br>timely fashion.</li>
    </ul>
    <p class="service-cta">BOOK AN APPOINTMENT NOW!</p>
  </section>
</div>
</body>
</html>
```